Quran Jar

So I need help designing bespoke jars which will contain religious quotes.

So there will be three jars in total sold either individually or in two or as a three.

Each Jar will have different contents and preferably a different colour scheme.

I want the packaging to be customised with my branding and logo and to make the product stand out I am thinking of packing it further in a cotton bag with my branding.

```html
<!DOCTYPE html>
<html lang="en">
<head>
<meta charset="utf-8">
<title>Serene Verses – Jar Labels</title>
<link rel="stylesheet" href="https://fonts.googleapis.com/css2?family=Quicksand:wght@600&family=Lato:wght@300;400&display=swap">
<style>
  :root {
    --bg-top: #ffffff;
    --bg-bottom: #c4c4c6;
    --quran: #244a34;
    --quran-band: #1b3a28;
    --hadith: #7b5b1f;
    --hadith-band: #5f4515;
    --dua: #f0f0f0;
    --dua-band: #d6d6d6;
    --brand-on-dark: #d3b56a;
    --brand-on-light: #8d6a28;
    --title-light: #f4f1ea;
    --title-dark: #3a3a3a;
    --tab-happiness: #f2d23c;
    --tab-sadness: #8fc6e8;
    --tab-anxiety: #b57fe0;
    --tab-gratefulness: #8dd68a;
    --tab-patience: #e09a2a;
    --tab-hope: #e2a7b8;
    --tab-forgiveness: #e2e2e2;
    --tab-love: #d21f1f;
  }
  * { box-sizing: border-box; margin: 0; padding: 0; }
  html, body { width: 1200px; height: 528px; overflow: hidden; }
  body {
    background: linear-gradient(180deg, var(--bg-top) 0%, var(--bg-bottom) 100%);
    font-family: "Lato", sans-serif;
    position: relative;
  }
  .label {
    position: absolute;
    top: 168px;
    width: 252px;
    height: 190px;
    display: flex;
    flex-direction: column;
    align-items: center;
    padding-top: 62px;
    box-shadow: 0 10px 24px rgba(0,0,0,0.12);
  }
  .label--quran { left: 93px; background: var(--quran); --band: var(--quran-band); --brand: var(--brand-on-dark); --title: var(--title-light); --tabtext: #e8e8e8; --body: #cfd8d2; }
  .label--hadith { left: 474px; background: var(--hadith); --band: var(--hadith-band); --brand: #e1c274; --title: var(--title-light); --tabtext: #f0e6d0; --body: #e6d8b8; }
  .label--dua { left: 856px; background: var(--dua); --band: var(--dua-band); --brand: var(--brand-on-light); --title: var(--title-dark); --tabtext: #555; --body: #666; }

  .brand {
    display: flex; align-items: center; gap: 5px;
    font-family: "Quicksand", sans-serif;
    font-weight: 600;
    font-size: 12px;
    color: var(--brand);
    letter-spacing: 0.2px;
  }
  .brand__dot { width: 7px; height: 7px; border-radius: 50%; background: var(--brand); }

  .product-title {
    margin-top: 6px;
    font-family: "Lato", sans-serif;
    font-weight: 300;
    font-size: 22px;
    line-height: 1;
    color: var(--title);
    letter-spacing: 0.5px;
  }
  .product-sub {
    font-weight: 300;
    font-size: 11px;
    line-height: 1;
    color: var(--title);
    margin-top: 1px;
  }

  .mood-tabs {
    position: absolute;
    left: 6px; right: 6px; top: 148px;
    display: flex;
  }
  .mood-tab { flex: 1 1 auto; display: flex; flex-direction: column; }
  .mood-tab::before { content: ""; height: 4px; background: var(--tab); border-radius: 2px 2px 0 0; }
  .mood-tab span {
    background: var(--band);
    color: var(--tabtext);
    font-size: 3.6px;
    text-align: center;
    padding: 1.5px 2px;
    letter-spacing: 0.2px;
    border-right: 0.5px solid rgba(255,255,255,0.35);
  }
  .mood-tab--happiness { --tab: var(--tab-happiness); flex-grow: 1.1; }
  .mood-tab--sadness { --tab: var(--tab-sadness); flex-grow: 1.2; }
  .mood-tab--anxiety { --tab: var(--tab-anxiety); flex-grow: 1.4; }
  .mood-tab--gratefulness { --tab: var(--tab-gratefulness); flex-grow: 1.5; }
  .mood-tab--patience { --tab: var(--tab-patience); flex-grow: 1.4; }
  .mood-tab--hope { --tab: var(--tab-hope); flex-grow: 1.4; }
  .mood-tab--forgiveness { --tab: var(--tab-forgiveness); flex-grow: 1.3; }
  .mood-tab--love { --tab: var(--tab-love); flex-grow: 0.9; }

  .label-copy {
    position: absolute;
    left: 22px; right: 22px; top: 166px;
    font-size: 3.4px;
    line-height: 1.35;
    text-align: center;
    color: var(--body);
  }
</style>
</head>
<body>

<section class="label label--quran" aria-label="Quran jar label">
  <div class="brand"><span class="brand__dot"></span>Serene Verses</div>
  <h1 class="product-title">QURAN</h1>
  <p class="product-sub">JAR</p>
  <div class="mood-tabs">
    <div class="mood-tab mood-tab--happiness"><span>HAPPINESS</span></div>
    <div class="mood-tab mood-tab--sadness"><span>SADNESS</span></div>
    <div class="mood-tab mood-tab--anxiety"><span>ANXIETY</span></div>
    <div class="mood-tab mood-tab--gratefulness"><span>GRATEFULNESS</span></div>
    <div class="mood-tab mood-tab--patience"><span>PATIENCE</span></div>
    <div class="mood-tab mood-tab--hope"><span>HOPE</span></div>
    <div class="mood-tab mood-tab--forgiveness"><span>FORGIVENESS</span></div>
    <div class="mood-tab mood-tab--love"><span>LOVE</span></div>
  </div>
  <p class="label-copy">Lorem ipsum dolor sit amet, consectetur adipiscing elit, sed do eiusmod tempor incididunt ut labore et dolore magna aliqua. Ut enim ad minim veniam, quis nostrud exercitation ullamco laboris nisi ut aliquip ex ea commodo consequat.</p>
</section>

<section class="label label--hadith" aria-label="Hadith jar label">
  <div class="brand"><span class="brand__dot"></span>Serene Verses</div>
  <h1 class="product-title">HADITH</h1>
  <p class="product-sub">JAR</p>
  <div class="mood-tabs">
    <div class="mood-tab mood-tab--happiness"><span>HAPPINESS</span></div>
    <div class="mood-tab mood-tab--sadness"><span>SADNESS</span></div>
    <div class="mood-tab mood-tab--anxiety"><span>ANXIETY</span></div>
    <div class="mood-tab mood-tab--gratefulness"><span>GRATEFULNESS</span></div>
    <div class="mood-tab mood-tab--patience"><span>PATIENCE</span></div>
    <div class="mood-tab mood-tab--hope"><span>HOPE</span></div>
    <div class="mood-tab mood-tab--forgiveness"><span>FORGIVENESS</span></div>
    <div class="mood-tab mood-tab--love"><span>LOVE</span></div>
  </div>
  <p class="label-copy">Lorem ipsum dolor sit amet, consectetur adipiscing elit, sed do eiusmod tempor incididunt ut labore et dolore magna aliqua. Ut enim ad minim veniam, quis nostrud exercitation ullamco laboris nisi ut aliquip ex ea commodo consequat.</p>
</section>

<section class="label label--dua" aria-label="Dua jar label">
  <div class="brand"><span class="brand__dot"></span>Serene Verses</div>
  <h1 class="product-title">DUA</h1>
  <p class="product-sub">JAR</p>
  <div class="mood-tabs">
    <div class="mood-tab mood-tab--happiness"><span>HAPPINESS</span></div>
    <div class="mood-tab mood-tab--sadness"><span>SADNESS</span></div>
    <div class="mood-tab mood-tab--anxiety"><span>ANXIETY</span></div>
    <div class="mood-tab mood-tab--gratefulness"><span>GRATEFULNESS</span></div>
    <div class="mood-tab mood-tab--patience"><span>PATIENCE</span></div>
    <div class="mood-tab mood-tab--hope"><span>HOPE</span></div>
    <div class="mood-tab mood-tab--forgiveness"><span>FORGIVENESS</span></div>
    <div class="mood-tab mood-tab--love"><span>LOVE</span></div>
  </div>
  <p class="label-copy">Lorem ipsum dolor sit amet, consectetur adipiscing elit, sed do eiusmod tempor incididunt ut labore et dolore magna aliqua. Ut enim ad minim veniam, quis nostrud exercitation ullamco laboris nisi ut aliquip ex ea commodo consequat.</p>
</section>

</body>
</html>
```